Vision, Mission and Culture Posters

We have written text paragraphs for our company vision and mission and need them made into a2 or a3 sized posters using our logo for inspiration for colour. Our company culture has 10 paragraphs and we'd like this to be a single poster of a2 or a1. Each poster should have the logo on and share common design. It's not a complex job really.

Industry/Entity Type

It Company

Requirements
Nice to have
• These will be going up on our office wall so need to be clear to read from a distance and look professional but also not stodgy.

```html
<!DOCTYPE html>
<html lang="en">
<head>
<meta charset="utf-8">
<title>Mission – Kerbside Bay Hire</title>
<link rel="stylesheet" href="https://fonts.googleapis.com/css2?family=Anton&family=Archivo+Black&family=Arvo:wght@700&family=Josefin+Slab:wght@300&family=Roboto+Condensed:wght@400&family=Roboto:wght@900&display=swap">
<style>
  :root {
    --yellow: #fff200;
    --red: #d7262e;
    --ink: #111111;
    --paper: #f5f5f2;
    --paper-edge: #ece6b4;
  }
  * { margin: 0; padding: 0; box-sizing: border-box; }
  html, body { width: 1200px; height: 849px; overflow: hidden; background: var(--paper); }
  .poster {
    position: relative;
    width: 1200px;
    height: 849px;
    overflow: hidden;
    background: radial-gradient(ellipse 62% 62% at 50% 52%, var(--paper) 70%, var(--paper-edge) 100%);
    color: var(--ink);
  }
  .poster__frame { position: absolute; inset: 0; }
  .brand {
    position: absolute;
    left: 110px; top: 58px;
    display: flex; align-items: center; gap: 14px;
    font-family: "Archivo Black", sans-serif;
    font-size: 30px;
    color: var(--ink);
    line-height: 1;
  }
  .brand__mark { width: 26px; height: 26px; background: var(--red); }
  .title-tag {
    position: absolute;
    left: 540px; top: 28px;
    width: 388px; height: 110px;
    background: var(--ink);
    border-radius: 12px;
    display: flex; align-items: center; justify-content: center;
    font-family: "Anton", sans-serif;
    font-size: 104px;
    letter-spacing: 2px;
    color: var(--yellow);
    line-height: 1;
    padding-top: 6px;
  }
  .headline { position: absolute; left: 0; top: 0; }
  .headline__lead {
    font-family: "Josefin Slab", serif; font-weight: 300;
    fill: none; stroke: var(--ink); stroke-width: 1.3;
  }
  .headline__verb { font-family: "Anton", sans-serif; fill: var(--ink); }
  .headline__accent {
    font-family: "Arvo", serif; font-weight: 700;
    fill: var(--yellow); stroke: var(--ink); stroke-width: 2.2; paint-order: stroke;
  }
  .headline__key { font-family: "Roboto", sans-serif; font-weight: 900; fill: var(--red); }
  .belief {
    position: absolute;
    left: 60px; right: 60px; top: 520px;
    text-align: center;
    font-family: "Archivo Black", sans-serif;
    font-size: 29px;
    line-height: 43px;
    letter-spacing: -0.3px;
  }
  .belief__highlight { color: var(--red); }
  .approach {
    position: absolute;
    left: 80px; right: 80px; top: 678px;
    text-align: center;
    font-family: "Roboto Condensed", sans-serif;
    font-size: 26px;
    line-height: 37px;
  }
</style>
</head>
<body>
<main class="poster">
  <svg class="poster__frame" width="1200" height="849" viewBox="0 0 1200 849" aria-hidden="true">
    <path d="M0 0 H1200 V66 C1150 100 1100 140 1075 158 C1060 168 1045 170 1020 168 L0 152 Z" fill="var(--yellow)"/>
    <path d="M0 152 L1020 168 C1045 170 1060 168 1075 158 C1100 140 1150 100 1200 66" fill="none" stroke="var(--ink)" stroke-width="2"/>
    <path d="M0 820 L1160 810 C1180 810 1192 814 1200 820 V849 H0 Z" fill="var(--red)" stroke="var(--ink)" stroke-width="2"/>
  </svg>

  <div class="brand"><span class="brand__mark"></span><span class="brand__name">Kerbside Bay Hire</span></div>

  <h1 class="title-tag">MISSION</h1>

  <svg class="headline" width="1200" height="849" viewBox="0 0 1200 849" role="heading" aria-level="2" aria-label="Our mission is to achieve great customer satisfaction">
    <text class="headline__lead" x="165" y="270" font-size="96" textLength="860" lengthAdjust="spacingAndGlyphs">OUR MISSION IS TO</text>
    <text class="headline__verb" transform="translate(233 495) rotate(-90)" font-size="78" textLength="210" lengthAdjust="spacingAndGlyphs">ACHIEVE</text>
    <text class="headline__accent" x="251" y="377" font-size="104" textLength="778" lengthAdjust="spacingAndGlyphs">GREAT CUSTOMER</text>
    <text class="headline__key" x="249" y="494" font-size="134" textLength="781" lengthAdjust="spacingAndGlyphs">SATISFACTION</text>
  </svg>

  <p class="belief">We believe our path to achieving this comes through giving a <span class="belief__highlight">simple yet thorough and friendly service</span> to our customers without unnecessary complication.</p>

  <p class="approach">We will achieve this through using the technology available to us, continual staff training and development, regular refinement of our practices and processes along with commitment to our roles and the foundations for building our success.</p>
</main>
</body>
</html>
```